Refresh Velquor Web Presence - www.velquor-sample.com

Velquor (www.velquor-sample.com)web site needs a makeover. It needs to be more modern, less cluttered, more corporate, prestigious, user friendly, impressive, up to date. We want a modern corporate image that encourages our business users to trust us and buy our products and services. They need to understand that they are dealing with a highly reputable, long established company, but one that is up to date and forward thinking.
1. Clean uncluttered design.
2. Domain Registration box and Countries (price) box to be collapsible and expandable.
3. All links on page need to be conserved for SEO but hidden from view.
4. Logo and general colour scheme need to be retained.
5. Phone number to be prominently displayed at top of page.
6. No calls to action (CTA) below the fold.
7. Sites we like: www.brinzal-sample.com, www.tundexa-sample.com,www.qop.com,www.plavion-sample.com, www.fismet-sample.com (busy but clear CTAs), www.yarmel-sample.com
Reason: We lost a lot of time to review over the holiday weekend. We need to have a chance to interact during business hours.
Target Market(s)
Small business to large enterprise
Industry/Entity Type
Business
Look and feel

```html
<!DOCTYPE html>
<html lang="en">
<head>
<meta charset="utf-8">
<title>Velquor — Website Hosting</title>
<link href="https://fonts.googleapis.com/css2?family=Oswald:wght@300;400;500&family=Open+Sans:wght@400;600;700&family=PT+Sans+Narrow:wght@400;700&display=swap" rel="stylesheet">
<style>
  :root {
    --navy: #33379a;
    --navy-dark: #2a2d86;
    --orange: #e2690f;
    --orange-light: #f08a2a;
    --ink: #2f2f2f;
    --ink-soft: #444;
    --sky: #dcecf8;
    --sky-deep: #a9cbe8;
    --grey-band: #e9e9e9;
    --grey-line: #cfcfcf;
    --white: #ffffff;
    --red-arrow: #d8322a;
  }
  * { margin: 0; padding: 0; box-sizing: border-box; }
  html, body { width: 1200px; height: 633px; overflow: hidden; background: var(--white); }
  body { position: relative; font-family: "Open Sans", Arial, sans-serif; color: var(--ink); }

  .top-bar {
    position: absolute; left: 0; top: 0; width: 1200px; height: 41px;
    background: linear-gradient(#3d42a6, var(--navy-dark));
    color: var(--white); font-size: 14px;
  }
  .chat-link { position: absolute; left: 94px; top: 11px; display: flex; align-items: center; gap: 6px; }
  .utility-links { position: absolute; left: 562px; top: 0; height: 41px; display: flex; align-items: center; white-space: nowrap; }
  .utility-links .phone { font-size: 17px; margin-right: 2px; }
  .utility-links span.sep { width: 1px; height: 16px; background: rgba(255,255,255,.45); margin: 0 12px; }
  .login-button {
    position: absolute; left: 1002px; top: 0; width: 84px; height: 41px;
    background: var(--orange); display: flex; align-items: center; justify-content: center; gap: 6px;
    font-size: 15px;
  }

  .hero {
    position: absolute; left: 0; top: 41px; width: 1200px; height: 462px; overflow: hidden;
    background: radial-gradient(ellipse at 45% 55%, #ffffff 0%, #f2f8fd 45%, var(--sky) 80%, var(--sky-deep) 100%);
  }
  .world-map {
    position: absolute; left: 195px; top: 100px; width: 530px; height: 330px;
    background: radial-gradient(ellipse, rgba(150,160,175,.28), rgba(150,160,175,0) 70%);
  }
  .server-art {
    position: absolute; left: 660px; top: 120px; width: 425px; height: 315px;
    background: linear-gradient(180deg, #9fb4c8 0%, #4f8fe6 45%, #7a8da3 100%);
    border-radius: 18px 18px 6px 6px; opacity: .9;
  }
  .brand { position: absolute; left: 98px; top: 33px; display: flex; align-items: center; gap: 10px; }
  .brand-dot { width: 46px; height: 46px; border-radius: 50%; background: var(--orange-light); }
  .brand-name { font-family: "Open Sans", sans-serif; font-weight: 700; font-size: 42px; line-height: 1; color: var(--navy); letter-spacing: -.5px; }

  .main-nav { position: absolute; left: 369px; top: 48px; display: flex; align-items: center; gap: 17px; font-weight: 700; font-size: 14.5px; color: #111; white-space: nowrap; }
  .main-nav .active {
    position: relative; background: var(--orange); color: var(--white); padding: 5px 10px; border-radius: 4px; margin-right: -8px;
  }
  .main-nav .active::after {
    content: ""; position: absolute; left: 50%; bottom: -7px; margin-left: -7px;
    border: 7px solid transparent; border-top-color: var(--orange); border-bottom: 0;
  }

  .hero-title { position: absolute; left: 100px; top: 127px; font-family: "Oswald", sans-serif; line-height: 1; font-weight: 400; }
  .hero-title .line-one { display: block; font-size: 82px; color: var(--ink); letter-spacing: 5px; }
  .hero-title .line-two { display: block; font-weight: 500; font-size: 104px; color: var(--orange); letter-spacing: 5px; margin-top: 0; margin-left: 22px; }
  .hero-tagline { position: absolute; left: 101px; top: 316px; font-family: "Oswald", sans-serif; font-weight: 300; font-size: 31px; line-height: 1.1; letter-spacing: 1.2px; color: var(--orange); white-space: nowrap; }

  .order-button {
    position: absolute; left: 100px; top: 380px; width: 243px; height: 59px;
    background: linear-gradient(var(--orange-light), #d55e08); border-radius: 8px;
    box-shadow: 0 2px 4px rgba(0,0,0,.3), inset 0 0 0 2px rgba(255,255,255,.35);
    color: var(--white); font-family: "Oswald", sans-serif; font-weight: 500; font-size: 31px;
    display: flex; align-items: center; justify-content: center; gap: 20px;
  }
  .pointer-arrow { position: absolute; left: 365px; top: 397px; }

  .slide-dots { position: absolute; left: 1021px; top: 420px; display: flex; gap: 5px; }
  .slide-dots span { width: 17px; height: 17px; border-radius: 50%; background: var(--navy); box-shadow: 0 1px 2px rgba(0,0,0,.4); }
  .slide-dots span.current { background: var(--orange); }

  .utility-band {
    position: absolute; left: 0; top: 503px; width: 1200px; height: 59px;
    background: linear-gradient(#f4f4f4, var(--grey-band)); border-top: 1px solid var(--grey-line);
  }
  .mailing-label { position: absolute; left: 97px; top: 14px; font-family: "PT Sans Narrow", sans-serif; font-size: 25px; color: var(--navy); }
  .mailing-field {
    position: absolute; left: 207px; top: 14px; width: 187px; height: 34px; border: 1px solid #bbb; border-right: 0;
    border-radius: 4px 0 0 4px; background: var(--white); font-size: 14px; color: #999; padding: 7px 9px;
  }
  .subscribe-button {
    position: absolute; left: 394px; top: 14px; width: 92px; height: 34px; border-radius: 0 4px 4px 0;
    background: var(--navy); color: var(--white); font-weight: 700; font-size: 15px; text-align: center; line-height: 34px;
  }
  .currency-label { position: absolute; left: 720px; top: 21px; font-size: 16px; font-weight: 600; color: var(--ink-soft); }
  .currency-select {
    position: absolute; left: 808px; top: 14px; width: 90px; height: 34px; background: var(--white);
    border: 1px solid #bbb; border-radius: 4px; font-weight: 600; font-size: 16px; padding: 6px 12px;
  }
  .caret { position: absolute; width: 0; height: 0; border: 6px solid transparent; border-top: 7px solid var(--orange); border-bottom: 0; }
  .currency-select .caret { right: 10px; top: 14px; }
  .country-button {
    position: absolute; left: 916px; top: 14px; width: 168px; height: 34px; background: var(--orange);
    border-radius: 4px; color: var(--white); font-family: "PT Sans Narrow", sans-serif; font-weight: 700; font-size: 19px;
    padding: 4px 16px; white-space: nowrap;
  }
  .country-button .caret, .login-button .caret { border-top-color: var(--white); position: static; display: inline-block; vertical-align: middle; margin-left: 4px; }

  .service-tabs {
    position: absolute; left: 0; top: 562px; width: 1200px; height: 71px;
    background: repeating-linear-gradient(0deg, #f7f7f7 0 2px, #fdfdfd 2px 4px);
  }
  .service-tabs ul { list-style: none; position: absolute; left: 93px; top: 32px; display: flex; font-size: 21.5px; color: var(--ink-soft); font-weight: 600; white-space: nowrap; }
  .service-tabs li { padding: 6px 14px 0; margin-right: 8px; height: 39px; }
  .service-tabs li.selected { background: linear-gradient(#e2e2e2, #f3f3f3); border-radius: 10px 10px 0 0; }
</style>
</head>
<body>
  <header class="top-bar">
    <div class="chat-link">
      <svg width="14" height="12" viewBox="0 0 14 12"><path d="M7 0C3 0 0 2.2 0 5c0 1.5.9 2.8 2.3 3.7L1.6 12l3.4-2.3c.6.1 1.3.2 2 .2 4 0 7-2.2 7-5S11 0 7 0z" fill="#fff"/></svg>
      Chat with us
    </div>
    <nav class="utility-links">
      <span class="phone">+1.5550142286</span><span class="sep"></span>
      Register<span class="sep"></span>Shopping Cart<span class="sep"></span>View Cart (0)
    </nav>
    <div class="login-button">Login <span class="caret"></span></div>
  </header>

  <section class="hero">
    <div class="world-map" role="img" aria-label="Dotted world map in soft grey"></div>
    <div class="server-art" role="img" aria-label="Illustration of blue glowing server towers"></div>

    <div class="brand"><span class="brand-dot"></span><span class="brand-name">Velquor</span></div>

    <nav class="main-nav">
      <span class="active">Domain Names</span>
      <span>IDN Domains</span><span>New gTLDs</span><span>Phone Numbers</span>
      <span>Hosting</span><span>Resellers</span><span>About Us</span>
    </nav>

    <h1 class="hero-title"><span class="line-one">WEBSITE</span><span class="line-two">HOSTING</span></h1>
    <p class="hero-tagline">FLEXIBLE WEB &amp; EMAIL PACKAGES</p>

    <div class="order-button">ORDER NOW
      <svg width="26" height="30" viewBox="0 0 26 30"><path d="M2 2 L24 15 L2 28 Z" fill="none" stroke="#fff" stroke-width="4" stroke-linejoin="round"/></svg>
    </div>
    <svg class="pointer-arrow" width="135" height="34" viewBox="0 0 135 34">
      <path d="M132 4 C100 10 60 22 6 12" fill="none" stroke="var(--red-arrow)" stroke-width="3" stroke-linecap="round"/>
      <path d="M18 2 L5 12 L20 22" fill="none" stroke="var(--red-arrow)" stroke-width="3" stroke-linecap="round" stroke-linejoin="round"/>
    </svg>

    <div class="slide-dots"><span></span><span></span><span class="current"></span></div>
  </section>

  <section class="utility-band">
    <span class="mailing-label">Mailing List</span>
    <div class="mailing-field">Enter email here</div>
    <div class="subscribe-button">Subscribe</div>
    <span class="currency-label">Currency</span>
    <div class="currency-select">USD<span class="caret"></span></div>
    <div class="country-button">Select Country <span class="caret"></span></div>
  </section>

  <nav class="service-tabs">
    <ul>
      <li class="selected">Domain Registration</li><li>IDN</li><li>Bulk Search</li>
      <li>Transfer</li><li>Renew</li><li>Map Search</li><li>PhNUM</li>
    </ul>
  </nav>
</body>
</html>
```